Coastline Premier Retreats Business Card Design

Design a business card for Coastline Premier Retreats. Look at the website for colors and reference. Card should have logo, name, title, office number, mobile number, email, URL and a tagline like, "Luxury Hotel & Resort Email Marketing" (This might change).

https://www.coastlinepremierretreats.example

The rest I will leave up to your imagination.

Contact Information for Business Card

Logo, name, title, office number, mobile number, email, URL and a tagline like, "Luxury Hotel & Resort Email Marketing" (This might change).

```html
<!DOCTYPE html>
<html lang="en">
<head>
<meta charset="utf-8">
<title>Coastline Premier Retreats – Business Card</title>
<link rel="stylesheet" href="https://fonts.googleapis.com/css2?family=Arimo:wght@400;700&display=swap">
<style>
  :root {
    --backdrop: #2b2b2b;
    --card: #1b1b1b;
    --accent: #f07c17;
    --ink: #ffffff;
    --ink-soft: #e6e6e6;
  }
  * { box-sizing: border-box; margin: 0; padding: 0; }
  html, body { width: 1200px; height: 900px; overflow: hidden; }
  body {
    background: var(--backdrop);
    font-family: "Arimo", Arial, sans-serif;
    color: var(--ink);
    position: relative;
  }
  .card {
    position: absolute;
    width: 620px;
    height: 354px;
    background: var(--card);
    border-bottom: 5px solid var(--accent);
    box-shadow: 0 18px 40px rgba(0,0,0,.55);
  }
  .card--front { left: 110px; top: 60px; }
  .card--back  { left: 470px; top: 480px; }

  .brand {
    display: flex;
    align-items: center;
    gap: 12px;
    font-weight: 700;
    text-transform: uppercase;
    color: var(--ink);
    white-space: nowrap;
  }
  .brand__mark { background: var(--accent); flex: none; }

  .card--front .brand {
    position: absolute; left: 0; right: 0; top: 160px;
    justify-content: center;
    font-size: 30px; letter-spacing: 2px;
  }
  .card--front .brand__mark { width: 18px; height: 18px; }

  .card--back .brand {
    position: absolute; left: 0; right: 0; top: 52px;
    justify-content: center;
    font-size: 22px; letter-spacing: 1.5px;
  }
  .card--back .brand__mark { width: 14px; height: 14px; }

  .identity {
    position: absolute; right: 336px; top: 128px;
    text-align: right;
  }
  .identity__name {
    color: var(--accent); font-weight: 700;
    font-size: 28px; letter-spacing: .5px; text-transform: uppercase;
  }
  .identity__title { font-size: 15px; margin-top: 4px; color: var(--ink-soft); }
  .identity__address { font-size: 14px; line-height: 1.45; margin-top: 12px; color: var(--ink-soft); }

  .divider {
    position: absolute; left: 304px; top: 126px;
    width: 1px; height: 118px; background: var(--accent);
  }

  .contacts {
    position: absolute; left: 322px; top: 130px;
    list-style: none; font-size: 13.5px; color: var(--ink-soft);
  }
  .contacts li { display: flex; align-items: center; gap: 9px; height: 27px; }
  .contacts svg { width: 13px; height: 13px; fill: var(--accent); flex: none; }

  .tagline {
    position: absolute; left: 0; right: 0; bottom: 36px;
    text-align: center; font-size: 15px; color: var(--ink-soft);
  }
</style>
</head>
<body>

<section class="card card--front" aria-label="Card front">
  <div class="brand"><span class="brand__mark"></span>Coastline Premier Retreats</div>
</section>

<section class="card card--back" aria-label="Card back">
  <div class="brand"><span class="brand__mark"></span>Coastline Premier Retreats</div>

  <div class="identity">
    <p class="identity__name">Daniel Reyes</p>
    <p class="identity__title">CEO/Founder</p>
    <p class="identity__address">Po Box, 48 Harbor Lane<br>Seaview, CA 90210</p>
  </div>

  <div class="divider"></div>

  <ul class="contacts">
    <li>
      <svg viewBox="0 0 16 16" aria-hidden="true"><path d="M4 0h8a1 1 0 0 1 1 1v14a1 1 0 0 1-1 1H4a1 1 0 0 1-1-1V1a1 1 0 0 1 1-1zm1 2v10h6V2zm3 11a1 1 0 1 0 0 2 1 1 0 0 0 0-2z"/></svg>
      555.214.7300
    </li>
    <li>
      <svg viewBox="0 0 16 16" aria-hidden="true"><path d="M3.6 1.2 6 3.6 4.6 5.5a9 9 0 0 0 5.9 5.9l1.9-1.4 2.4 2.4-1.6 2.4C7 14.8 1.2 9 .8 2.8z"/></svg>
      +34 600 555 214
    </li>
    <li>
      <svg viewBox="0 0 16 16" aria-hidden="true"><path d="M0 3h16v10H0zm1.5 1.5 6.5 4.8 6.5-4.8z"/></svg>
      info@coastlinepremierretreats.example
    </li>
    <li>
      <svg viewBox="0 0 16 16" aria-hidden="true"><path d="M8 0a8 8 0 1 0 0 16A8 8 0 0 0 8 0zm0 1.5c.9 0 1.9 1.9 2.2 5.5H5.8C6.1 3.4 7.1 1.5 8 1.5zM5.8 9h4.4c-.3 3.6-1.3 5.5-2.2 5.5S6.1 12.6 5.8 9zM1.6 7a6.5 6.5 0 0 1 3.1-4.6A13 13 0 0 0 4.3 7zm0 2h2.7c.1 1.8.4 3.4.9 4.6A6.5 6.5 0 0 1 1.6 9zm10.1 0h2.7a6.5 6.5 0 0 1-3.6 4.6c.5-1.2.8-2.8.9-4.6zm0-2a13 13 0 0 0-.4-4.6A6.5 6.5 0 0 1 14.4 7z"/></svg>
      www.coastlinepremierretreats.example
    </li>
  </ul>

  <p class="tagline">Luxury Hotel &amp; Resort Email Marketing</p>
</section>

</body>
</html>
```